Vacation Rental Postcard Design

The Kingfisher's Perch is a vacation rental cottage. We want a postcard that can be used as promotional give-aways for visitors as well as something that can be given to the tourism board and local merchants to help us promote the rental.

Our tag line is" The Kingfisher's Perch - the finest perch on the ridge!". Should also include "Snohomish, WA USA"

We have also used "Come see what all of the buzz is about"

Want to include our info in small print on the mailing side portion of the postcard:

KLWT: www.klwtstays.example/417294
Chatterly: www.chatterly.example/thefinestperchontheridge

Target Market(s)

Couples, romantic, honeymooners, coming for wine tasting, hot air ballooning, hiking, enjoying nature

Industry/Entity Type

Tourism

```html
<!DOCTYPE html>
<html lang="en">
<head>
<meta charset="utf-8">
<title>The Kingfisher's Perch – Postcard</title>
<link href="https://fonts.googleapis.com/css2?family=Great+Vibes&family=PT+Sans:ital,wght@0,400;0,700;1,700&display=swap" rel="stylesheet">
<style>
  :root {
    --backdrop: #efe9df;
    --card-green: #8fb46a;
    --card-green-dark: #6f9550;
    --frame-green: #2f5a2c;
    --wood-light: #8a5a33;
    --wood-dark: #4e2f18;
    --tag-lime: #b8d432;
    --ink-white: #ffffff;
    --sand: #d9cfa8;
    --url-red: #e0553a;
    --brand-blue: #3b5b9a;
    --line-grey: #b9b9b9;
    --paper: #ffffff;
    --script: "Great Vibes", cursive;
    --sans: "PT Sans", sans-serif;
  }
  * { box-sizing: border-box; margin: 0; padding: 0; }
  html, body { width: 1200px; height: 500px; overflow: hidden; background: var(--backdrop); }
  .canvas { position: relative; width: 1200px; height: 500px; }

  .card { position: absolute; top: 18px; height: 432px; box-shadow: 0 2px 6px rgba(0,0,0,.25); overflow: hidden; }
  .front { left: 30px; width: 568px; background: radial-gradient(circle at 60% 40%, #9cc076, var(--card-green) 70%, var(--card-green-dark)); }
  .back { left: 613px; width: 559px; background: var(--paper); }

  .photo { position: absolute; border: 3px solid var(--frame-green); }

  /* front */
  .brand-mark { position: absolute; left: 14px; top: 30px; width: 130px; text-align: center; }
  .brand-mark .dot { display: inline-block; width: 34px; height: 34px; border-radius: 50%; background: var(--frame-green); margin-bottom: 6px; }
  .brand-mark .name { font-family: var(--sans); font-weight: 700; font-size: 15px; color: var(--frame-green); line-height: 1.1; }

  .title-banner { position: absolute; left: 153px; top: 0; width: 415px; height: 92px;
    background: linear-gradient(90deg, var(--wood-dark), var(--wood-light) 45%, var(--wood-dark)); }
  .title-banner .name { position: absolute; left: 8px; top: 4px; font-family: var(--script); font-size: 40px; color: var(--ink-white); white-space: nowrap; }
  .title-banner .tag { position: absolute; left: 14px; top: 56px; font-family: var(--sans); font-weight: 700; font-size: 22px; color: var(--tag-lime); }

  .hero { left: 156px; top: 94px; width: 380px; height: 213px;
    background: linear-gradient(180deg, #5e6270 0%, #8a8c94 35%, #3f5a33 60%, #2e4a28 100%); }
  .hero .buzz { position: absolute; left: 22px; bottom: 8px; font-family: var(--sans); font-weight: 700; font-style: italic; font-size: 20px; color: var(--ink-white); }
  .house-side { left: 20px; top: 148px; width: 128px; height: 159px; background: linear-gradient(180deg, #7fa4cf, #3f5e3a 55%, #8d8a7c); }
  .room-1 { left: 20px; top: 319px; width: 128px; height: 95px; background: linear-gradient(180deg, #8a6a48, #b89b74); }
  .room-2 { left: 153px; top: 319px; width: 128px; height: 95px; background: linear-gradient(180deg, #a58a54, #e6e1d4); }
  .room-3 { left: 286px; top: 319px; width: 128px; height: 95px; background: linear-gradient(180deg, #c9b98c, #6b4e35); }
  .house-rear { left: 419px; top: 319px; width: 117px; height: 95px; background: linear-gradient(180deg, #5a8fd0, #3a3a36 55%, #5f7a44); }

  /* back */
  .message-panel { position: absolute; left: 0; top: 0; width: 297px; height: 330px; background: radial-gradient(circle at 60% 40%, #9ab474, #7e9e5c 80%); }
  .message-panel .name { position: absolute; left: 24px; top: 14px; font-family: var(--script); font-size: 29px; color: var(--ink-white); white-space: nowrap; }
  .message-panel .tag { position: absolute; left: 32px; top: 52px; font-family: var(--sans); font-weight: 700; font-size: 15px; color: var(--ink-white); }
  .message-panel .copy { position: absolute; left: 32px; top: 80px; width: 262px; font-family: var(--sans); font-weight: 700; font-size: 12.5px; line-height: 1.55; color: var(--ink-white); }
  .message-panel .copy p + p { margin-top: 8px; }
  .sunset { left: 44px; top: 172px; width: 208px; height: 152px; border: 6px solid #f4ecd0; transform: rotate(-3deg);
    background: linear-gradient(180deg, #d9607a 0%, #f08a78 40%, #3a2a38 75%, #1e1a22 100%); }

  .contact-band { position: absolute; left: 0; top: 330px; width: 297px; height: 102px; background: var(--sand); text-align: center; }
  .contact-band .channels { display: flex; justify-content: center; align-items: center; gap: 18px; margin-top: 12px; font-family: var(--sans); font-weight: 700; font-size: 19px; line-height: 24px; color: var(--brand-blue); }
  .contact-band .chip { display: inline-block; width: 20px; height: 20px; background: var(--brand-blue); vertical-align: -3px; margin-right: 6px; }
  .contact-band .urls { margin-top: 5px; font-family: var(--sans); font-weight: 700; font-size: 12px; line-height: 1.4; color: var(--url-red); }
  .contact-band .location { margin-top: 2px; font-family: var(--sans); font-weight: 700; font-size: 12px; line-height: 1.4; color: var(--frame-green); }

  .address-side { position: absolute; left: 297px; top: 0; width: 262px; height: 432px; }
  .address-side .brand-mark { left: 24px; top: 30px; width: 110px; }
  .stamp-box { position: absolute; left: 157px; top: 14px; width: 90px; height: 93px; border: 1px solid var(--line-grey); }
  .address-line { position: absolute; left: 30px; width: 215px; height: 1px; background: var(--line-grey); }
  .line-1 { top: 212px; } .line-2 { top: 247px; } .line-3 { top: 282px; } .line-4 { top: 317px; }
</style>
</head>
<body>
<div class="canvas">

  <section class="card front">
    <div class="brand-mark">
      <span class="dot"></span>
      <div class="name">The Kingfisher's Perch</div>
    </div>
    <header class="title-banner">
      <div class="name">The Kingfisher's Perch</div>
      <div class="tag">The Finest On The Ridge</div>
    </header>
    <div class="photo hero" role="img" aria-label="Photo of the cottage grounds with evergreens and a rainbow">
      <div class="buzz">Come see what all of the buzz is about</div>
    </div>
    <div class="photo house-side" role="img" aria-label="Photo of the green cottage exterior"></div>
    <div class="photo room-1" role="img" aria-label="Photo of the living room"></div>
    <div class="photo room-2" role="img" aria-label="Photo of the bedroom"></div>
    <div class="photo room-3" role="img" aria-label="Photo of the dining area"></div>
    <div class="photo house-rear" role="img" aria-label="Photo of the cottage from the garden"></div>
  </section>

  <section class="card back">
    <div class="message-panel">
      <div class="name">The Kingfisher's Perch</div>
      <div class="tag">The Finest Perch On The Ridge</div>
      <div class="copy">
        <p>Private view cottage on two country acres, Romantic, refreshing, relaxing, reconnect.</p>
        <p>1 bedroom, 1.5 bath apartment, spectacular mountain, valley and river view.</p>
      </div>
      <div class="photo sunset" role="img" aria-label="Photo of a pink sunset over the valley"></div>
    </div>
    <div class="contact-band">
      <div class="channels">
        <span><span class="chip"></span>Chatterly</span>
        <span>KLWT</span>
      </div>
      <div class="urls">
        KLWT: www.klwtstays.example/417294<br>
        www.chatterly.example/thefinestperchontheridge
      </div>
      <div class="location">Snohomish, WA USA</div>
    </div>
    <div class="address-side">
      <div class="brand-mark">
        <span class="dot"></span>
        <div class="name">The Kingfisher's Perch</div>
      </div>
      <div class="stamp-box"></div>
      <div class="address-line line-1"></div>
      <div class="address-line line-2"></div>
      <div class="address-line line-3"></div>
      <div class="address-line line-4"></div>
    </div>
  </section>

</div>
</body>
</html>
```